Veltra Metrics New Website for Health Benefits Plan Decisioneering Tool Launch

Veltra Metrics is a SaaS provider of health benefits comparison tools. We need a new simple SaaS focused website to direct customers to our product

Target Market(s)

General Public comparing their health benefits plans from their employer or from the state exchanges in the US

Coding

Coded - Design and coding required

Number of Pages Required

3 page

Requirements
Must have
• Main page - "Know the Best Health Benefits Plan for You!"
Graphic of a person looking over papers on their desk
Compare Now button to link to SaaS product
About Us
Product Page

https://plimbo.example/top-app-pages/

```html
<!DOCTYPE html>
<html lang="en">
<head>
<meta charset="utf-8">
<title>Veltra Metrics — Know the Best Health Benefits Plan for You</title>
<link href="https://fonts.googleapis.com/css2?family=Roboto+Slab:wght@300;400&family=Open+Sans:ital,wght@0,400;0,600;0,700;1,400&display=swap" rel="stylesheet">
<style>
:root{
  --blue:#2ba6e1;
  --blue-light:#4bb8ea;
  --blue-pale:#eaf6fd;
  --blue-deep:#1d6f9e;
  --ink:#333a40;
  --grey:#7a7f85;
  --white:#ffffff;
  --star:#f5b400;
}
*{box-sizing:border-box;margin:0;padding:0}
html,body{width:1200px;height:4651px;overflow:hidden}
body{font-family:"Open Sans",Arial,sans-serif;color:var(--ink);background:var(--white);position:relative}
.abs{position:absolute}
.serif{font-family:"Roboto Slab",Georgia,serif;font-weight:300}
.pill{display:flex;align-items:center;justify-content:center;border-radius:24px;font-size:12px;font-weight:700;letter-spacing:1px;text-transform:uppercase}
.pill-white{background:var(--white);color:var(--blue)}
.pill-blue{background:var(--blue);color:var(--white);box-shadow:0 4px 10px rgba(43,166,225,.3)}
.pill .arrow{width:13px;height:13px;border-radius:50%;background:var(--white);margin-left:8px;position:relative}
.pill .arrow::after{content:"";position:absolute;left:4px;top:3px;border:3.5px solid transparent;border-left:5px solid var(--blue)}
.section-title{position:absolute;left:0;width:1200px;text-align:center;font-size:40px;letter-spacing:1px;color:var(--ink)}
.title-bar{position:absolute;left:565px;width:70px;height:3px;background:var(--blue)}

/* hero */
.hero{position:absolute;left:0;top:0;width:1200px;height:650px;background:linear-gradient(160deg,#2ea9e3 0%,#36ade5 60%,#42b4e8 100%);overflow:hidden}
.brand{font-family:"Roboto Slab",Georgia,serif;font-weight:400;font-size:22px;letter-spacing:1px;color:var(--white);text-transform:uppercase}
.nav a{position:absolute;top:40px;font-size:13px;color:var(--white);text-decoration:none}
.nav a.active{border-bottom:1px solid var(--white);padding-bottom:2px}
.hero h1{position:absolute;left:110px;top:210px;font-size:40px;line-height:44px;color:var(--white);text-transform:uppercase;letter-spacing:.5px}
.hero p{position:absolute;left:110px;top:318px;font-size:12.5px;color:var(--white)}
.dots span{position:absolute;top:539px;border:2px solid var(--white);border-radius:50%}

/* about */
.about-text{position:absolute;left:190px;top:800px;width:820px;text-align:center;font-size:13.5px;line-height:22px;color:var(--grey)}
.feature{position:absolute;top:897px;width:306px;height:300px;text-align:center;background:var(--white)}
.feature.raised{box-shadow:0 2px 14px rgba(0,0,0,.12)}
.feature.raised::after{content:"";position:absolute;left:0;bottom:0;width:100%;height:7px;background:var(--blue)}
.feature .icon{position:absolute;left:100px;top:30px;width:108px;height:108px;border-radius:50%;border:2px solid #e6eef3;background:radial-gradient(circle,#d9eef9 0 30%,#fff 31%)}
.feature h3{position:absolute;top:152px;width:100%;font-size:18px;font-weight:600}
.feature p{position:absolute;top:184px;left:40px;width:226px;font-size:12.5px;line-height:21.5px;color:var(--grey)}

/* what we do */
.what{position:absolute;left:0;top:1294px;width:1200px;height:542px;background:var(--blue-pale)}
.what h2{position:absolute;left:110px;top:72px;font-size:40px;letter-spacing:1px}
.what .bar{position:absolute;left:110px;top:136px;width:70px;height:3px;background:var(--blue)}
.what p{position:absolute;left:110px;width:455px;font-size:12.5px;line-height:21.7px;color:var(--grey)}

/* products */
.product{position:absolute;top:2013px;width:307px;height:334px;background:var(--white);box-shadow:0 2px 12px rgba(0,0,0,.1);overflow:hidden}
.product .art{position:absolute;left:40px;top:20px;width:230px;height:165px;border-radius:50%/45%}
.product .ribbon{position:absolute;left:0;top:0;width:0;height:0;border-top:72px solid var(--blue);border-right:72px solid transparent}
.product .ribbon span{position:absolute;left:6px;top:-62px;transform:rotate(-45deg);font-size:10px;color:var(--white);font-weight:600;letter-spacing:.5px}
.product .copy{position:absolute;left:20px;top:198px;border-left:2px solid var(--blue);padding-left:18px;width:270px;height:112px}
.product h4{font-size:18px;color:var(--ink);margin-top:12px}
.product p{font-size:12px;line-height:21.5px;color:var(--grey);margin-top:8px}

/* testimonials */
.voices{position:absolute;left:0;top:2518px;width:1200px;height:726px}
.quote-card{position:absolute;top:2774px;width:309px;height:327px;background:var(--white);text-align:center}
.quote-card .mark{position:absolute;top:14px;width:100%;font-family:Georgia,serif;font-size:50px;line-height:50px;color:var(--blue);font-weight:700}
.quote-card p{position:absolute;top:60px;left:28px;width:253px;font-size:12.5px;line-height:21.7px;font-style:italic;color:var(--grey)}
.quote-card .stars{position:absolute;top:170px;left:0;width:100%;display:flex;justify-content:center;gap:3px}
.quote-card .avatar{position:absolute;top:204px;left:120px;width:68px;height:68px;border-radius:50%;background:linear-gradient(160deg,#c9d3db,#7d8a95);border:3px solid #eef2f5}
.quote-card .name{position:absolute;top:283px;width:100%;font-size:16px;color:var(--ink)}

/* blog */
.post{position:absolute;top:3406px;width:471px}
.post .photo{width:471px;height:273px}
.post h4{margin-top:33px;text-align:center;font-size:17px;font-weight:600;letter-spacing:1px}
.post .date{margin-top:8px;text-align:center;font-size:12px;color:var(--blue)}
.post p{margin:8px auto 0;width:400px;text-align:center;font-size:12.5px;line-height:21.5px;color:var(--grey)}
.post .pill{margin:24px auto 0;width:173px;height:45px}
.partner{position:absolute;top:3978px;height:60px;width:130px;border-radius:10px;background:#c9ccd0;opacity:.7}

/* footer */
.footer{position:absolute;left:0;top:4133px;width:1200px;height:518px}
.footer h5{position:absolute;top:4305px;font-size:21px;font-weight:600;color:var(--white)}
.footer-text{position:absolute;font-size:13.5px;line-height:22px;color:var(--white)}
.links a{position:absolute;left:421px;font-size:13.5px;color:var(--white);text-decoration:none}
.contact{position:absolute;left:590px;font-size:13.5px;color:var(--white);display:flex;align-items:center;gap:12px}
.social span{position:absolute;top:4473px;width:40px;height:40px;border-radius:50%;background:var(--white)}
</style>
</head>
<body>

<!-- HERO -->
<header class="hero">
  <svg class="abs" style="left:0;top:0" width="1200" height="650" aria-hidden="true">
    <path d="M0 540 C 180 640 380 600 600 560 C 820 520 1000 560 1200 610 L1200 650 L0 650Z" fill="#7fcbef" opacity=".5"/>
    <path d="M0 575 C 200 660 420 620 640 590 C 860 560 1040 600 1200 640 L1200 650 L0 650Z" fill="#ffffff"/>
    <path d="M760 80 C 900 40 1090 110 1100 260 C 1110 400 1010 500 870 495 C 740 490 700 380 715 270 C 725 180 700 110 760 80Z" fill="#ffffff"/>
    <path d="M770 100 C 890 60 1060 120 1070 260 C 1080 390 990 478 870 478 C 755 478 718 380 728 275 C 736 190 715 128 770 100Z" fill="url(#photo)" role="img" aria-label="Photo of a man at his desk reviewing papers beside a laptop"/>
    <defs><linearGradient id="photo" x1="0" y1="0" x2="1" y2="1"><stop offset="0" stop-color="#8c8f8d"/><stop offset=".5" stop-color="#b7b3ab"/><stop offset="1" stop-color="#e4e2de"/></linearGradient></defs>
  </svg>
  <div class="abs brand" style="left:112px;top:28px">Veltra Metrics</div>
  <nav class="nav">
    <a class="active" style="left:408px" href="#">Home</a>
    <a style="left:480px" href="#">About us</a>
    <a style="left:574px" href="#">Product</a>
    <a style="left:658px" href="#">Services</a>
    <a style="left:746px" href="#">Blog</a>
    <a style="left:811px" href="#">Contact us</a>
  </nav>
  <div class="abs pill pill-white" style="left:915px;top:28px;width:173px;height:44px;font-weight:600">Start Free Trial</div>
  <h1 class="serif">Know the best health<br>benefits plan for you!</h1>
  <p>Lorem ipsum dolor sit amet, consectetur adipiscing elit, sed do eiusmod temporalique.</p>
  <div class="abs pill pill-white" style="left:110px;top:355px;width:173px;height:45px">Compare&nbsp;&nbsp;Now</div>
  <div class="dots">
    <span style="left:110px;width:17px;height:17px"></span>
    <span style="left:134px;width:12px;height:12px;top:542px"></span>
    <span style="left:154px;width:12px;height:12px;top:542px"></span>
  </div>
</header>

<!-- ABOUT -->
<h2 class="section-title serif" style="top:715px">ABOUT VELTRA METRICS</h2>
<div class="title-bar" style="top:778px"></div>
<p class="about-text">Lorem ipsum dolor sit amet, consectetur adipiscing elit, sed do eiusmod tempor incididunt ut labore et dolore magna aliqua. Ut enim ad minim veniam, quis nostrud exercitation ullamco laboris nisi ut aliquip ex ea commodo consequat. Duis aute irure dolor in reprehenderit in voluptate velit esse cillum dolore eu</p>
<div class="feature" style="left:110px">
  <div class="icon" role="img" aria-label="Cloud computing icon"></div>
  <h3>Voluptatem</h3>
  <p>Lorem ipsum dolor sit amet, consec tetur adipiscing elit, sed do eiusmod tempor incididunt</p>
</div>
<div class="feature raised" style="left:447px">
  <div class="icon" role="img" aria-label="Hand holding a heart icon"></div>
  <h3>Voluptatem</h3>
  <p>Lorem ipsum dolor sit amet, consec tetur adipiscing elit, sed do eiusmod tempor incididunt</p>
</div>
<div class="feature" style="left:784px">
  <div class="icon" role="img" aria-label="Clipboard checklist icon"></div>
  <h3>Voluptatem</h3>
  <p>Lorem ipsum dolor sit amet, consec tetur adipiscing elit, sed do eiusmod tempor incididunt</p>
</div>

<!-- WHAT WE DO -->
<section class="what">
  <h2 class="serif">WHAT WE DO</h2>
  <div class="bar"></div>
  <p style="top:160px">Lorem ipsum dolor sit amet, consectetur adipiscing elit, sed do eiusmod tempor incididunt ut labore et dolore magna aliqua. Ut enim ad minim veniam, quis nostrud exercitation ullamco laboris nisi ut aliquip ex ea commodo consequat. Duis aute irure dolor in reprehenderit in voluptate velit esse cillum dolore eu fugiat nulla pariatur. Excepteur sint occaecat cupidatat non proident, sunt in culpa qui officia deserunt mollit anim id est laborum.</p>
  <p style="top:311px">Lorem ipsum dolor sit amet, consectetur adipiscing elit, sed do eiusmod tempor incididunt ut labore et dolore magna aliqua. Ut enim ad minim veniam, quis nostrud exercitation ullamco laboris nisi ut aliquip ex ea commodo consequat. Duis aute irure dolor in reprehenderit</p>
  <div class="abs pill pill-blue" style="left:110px;top:418px;width:173px;height:45px">Learn&nbsp;&nbsp;More<span class="arrow"></span></div>
  <svg class="abs" style="left:600px;top:40px" width="590" height="470" aria-hidden="true">
    <path d="M250 20 C 420 -30 580 80 578 240 C 576 380 470 460 340 455 C 250 452 200 410 180 360 L 180 120 C 190 70 210 35 250 20Z" fill="var(--blue)"/>
    <path d="M30 230 C 20 130 110 70 220 90 C 330 110 430 120 430 230 C 430 330 330 380 200 380 C 90 380 36 320 30 230Z" fill="url(#scene)" role="img" aria-label="Illustration of a woman reading a book at a desk with a lamp and a potted plant"/>
    <defs><linearGradient id="scene" x1="0" y1="0" x2="1" y2="1"><stop offset="0" stop-color="#e6e4f6"/><stop offset="1" stop-color="#f6d9c9"/></linearGradient></defs>
  </svg>
</section>

<!-- PRODUCTS -->
<h2 class="section-title serif" style="top:1908px">OUR PRODUCT</h2>
<div class="title-bar" style="top:1972px"></div>
<div class="product" style="left:110px">
  <div class="art" style="background:radial-gradient(circle,#3f8fe0 0 35%,#dbeefb 36% 70%,#fff 71%)" role="img" aria-label="SaaS cloud server illustration"></div>
  <div class="ribbon"><span>TRIAL</span></div>
  <div class="copy"><h4 class="serif">NEMO ENIM IPSAM</h4><p>Sed ut perspiciatis unde omnis iste natus error sit voluptatem accusantium doloremque</p></div>
</div>
<div class="product" style="left:447px">
  <div class="art" style="background:radial-gradient(circle,#5c8fe8 0 28%,#e6eefb 29% 70%,#fff 71%)" role="img" aria-label="SaaS network diagram illustration"></div>
  <div class="ribbon"><span>TRIAL</span></div>
  <div class="copy"><h4 class="serif">NEMO ENIM IPSAM</h4><p>Sed ut perspiciatis unde omnis iste natus error sit voluptatem accusantium doloremque</p></div>
</div>
<div class="product" style="left:783px">
  <div class="art" style="background:radial-gradient(ellipse at 50% 65%,#d9e7c8 0 34%,#fff 35%)" role="img" aria-label="SaaS cloud with connected devices illustration"></div>
  <div class="ribbon"><span>TRIAL</span></div>
  <div class="copy"><h4 class="serif">NEMO ENIM IPSAM</h4><p>Sed ut perspiciatis unde omnis iste natus error sit voluptatem accusantium doloremque</p></div>
</div>
<div class="abs pill pill-blue" style="left:514px;top:2376px;width:173px;height:45px">Learn&nbsp;&nbsp;More<span class="arrow"></span></div>

<!-- TESTIMONIALS -->
<section class="voices">
  <svg class="abs" style="left:0;top:0" width="1200" height="726" aria-hidden="true">
    <path d="M0 40 C 200 -10 420 30 640 60 C 860 90 1040 40 1200 20 L1200 726 L0 726Z" fill="#7fcbef"/>
    <path d="M0 90 C 220 40 460 110 700 90 C 920 72 1060 40 1200 70 L1200 726 L0 726Z" fill="var(--blue)"/>
    <path d="M0 560 C 240 610 480 540 720 570 C 940 600 1080 560 1200 530 L1200 726 L0 726Z" fill="#5dbdec"/>
    <path d="M0 640 C 220 600 460 690 700 665 C 920 640 1060 680 1200 660 L1200 726 L0 726Z" fill="#ffffff"/>
  </svg>
  <h2 class="section-title serif" style="top:170px;color:var(--white);font-size:31px">WHAT OUR CUSTOMER ARE SAYING</h2>
  <div class="title-bar" style="top:226px;background:var(--white)"></div>
</section>
<div class="quote-card" style="left:112px">
  <div class="mark">”</div>
  <p>“Lorem ipsum dolor sit amet, consectetur adipiscing elit, sed do eiusmod tempor incididunt ut labore et dolore magna aliqua. Ut enim ad minim veniam, quis nostrud exercitation ullamco laboris”</p>
  <div class="stars"><svg width="86" height="14" viewBox="0 0 86 14"><g fill="var(--star)"><path id="st" d="M7 0l2 4.5 5 .6-3.7 3.3 1 4.9L7 10.8 2.7 13.3l1-4.9L0 5.1l5-.6z"/><use href="#st" x="18"/><use href="#st" x="36"/><use href="#st" x="54"/><use href="#st" x="72"/></g></svg></div>
  <div class="avatar" role="img" aria-label="Customer portrait"></div>
  <div class="name">@Mara&nbsp;&nbsp;Lind</div>
</div>
<div class="quote-card" style="left:445px">
  <div class="mark">”</div>
  <p>“Lorem ipsum dolor sit amet, consectetur adipiscing elit, sed do eiusmod tempor incididunt ut labore et dolore magna aliqua. Ut enim ad minim veniam, quis nostrud exercitation ullamco laboris”</p>
  <div class="stars"><svg width="86" height="14" viewBox="0 0 86 14"><g fill="var(--star)"><use href="#st"/><use href="#st" x="18"/><use href="#st" x="36"/><use href="#st" x="54"/><use href="#st" x="72"/></g></svg></div>
  <div class="avatar" role="img" aria-label="Customer portrait"></div>
  <div class="name">@Mara&nbsp;&nbsp;Lind</div>
</div>
<div class="quote-card" style="left:779px">
  <div class="mark">”</div>
  <p>“Lorem ipsum dolor sit amet, consectetur adipiscing elit, sed do eiusmod tempor incididunt ut labore et dolore magna aliqua. Ut enim ad minim veniam, quis nostrud exercitation ullamco laboris”</p>
  <div class="stars"><svg width="86" height="14" viewBox="0 0 86 14"><g fill="var(--star)"><use href="#st"/><use href="#st" x="18"/><use href="#st" x="36"/><use href="#st" x="54"/><use href="#st" x="72"/></g></svg></div>
  <div class="avatar" role="img" aria-label="Customer portrait"></div>
  <div class="name">@Mara&nbsp;&nbsp;Lind</div>
</div>

<!-- BLOG -->
<h2 class="section-title serif" style="top:3308px">OUR BLOG</h2>
<div class="title-bar" style="top:3372px"></div>
<article class="post" style="left:112px">
  <div class="photo" role="img" aria-label="Photo of a doctor holding a green apple" style="background:linear-gradient(120deg,#b9b4ad,#e9e7e3 55%,#c9c3bb)"></div>
  <h4>Lorem ipsum dolor sit amet, consectetur</h4>
  <div class="date">&#9638;&nbsp; August 20,2020</div>
  <p>Lorem ipsum dolor sit amet, consectetur adipiscing elit, sed do eiusmod tempor incididunt ut labore et dolore magna aliqua.</p>
  <div class="pill pill-blue">Learn&nbsp;&nbsp;More<span class="arrow"></span></div>
</article>
<article class="post" style="left:617px">
  <div class="photo" role="img" aria-label="Photo of hands using a tablet showing a SaaS diagram on a desk" style="background:linear-gradient(120deg,#d8d6d2,#2b2d30 50%,#cfcac3)"></div>
  <h4>Lorem ipsum dolor sit amet, consectetur</h4>
  <div class="date">&#9638;&nbsp; August 20,2020</div>
  <p>Lorem ipsum dolor sit amet, consectetur adipiscing elit, sed do eiusmod tempor incididunt ut labore et dolore magna aliqua.</p>
  <div class="pill pill-blue">Learn&nbsp;&nbsp;More<span class="arrow"></span></div>
</article>
<div class="partner" role="img" aria-label="Partner badge" style="left:112px;height:50px;top:3983px"></div>
<div class="partner" role="img" aria-label="Partner badge" style="left:358px"></div>
<div class="partner" role="img" aria-label="Partner badge" style="left:546px;width:128px;height:80px;top:3968px;border-radius:50%"></div>
<div class="partner" role="img" aria-label="Partner badge" style="left:736px"></div>
<div class="partner" role="img" aria-label="Partner badge" style="left:966px;height:50px;top:3983px"></div>

<!-- FOOTER -->
<footer class="footer">
  <svg class="abs" style="left:0;top:0" width="1200" height="518" aria-hidden="true">
    <path d="M0 20 C 200 80 420 10 640 30 C 860 50 1040 10 1200 0 L1200 518 L0 518Z" fill="#7fcbef"/>
    <path d="M0 80 C 240 40 480 110 720 90 C 940 72 1080 110 1200 80 L1200 518 L0 518Z" fill="var(--blue)"/>
    <line x1="110" y1="442" x2="1088" y2="442" stroke="#ffffff" stroke-opacity=".5"/>
  </svg>
</footer>
<div class="abs brand" style="left:110px;top:4314px">Veltra Metrics</div>
<p class="footer-text" style="left:110px;top:4366px;width:250px">Lorem ipsum dolor sit amet, consectetur adipiscing elit, sed doLorem ipsum dolor sit amet, consectetur adipiscing elit, sed do</p>
<h5 style="position:absolute;left:417px;top:4305px;font-size:21px;font-weight:600;color:var(--white)">Useful&nbsp; Links</h5>
<div class="links">
  <a style="top:4356px" href="#">Our Services</a>
  <a style="top:4387px" href="#">About Us</a>
  <a style="top:4418px" href="#">Product</a>
  <a style="top:4449px" href="#">Blog</a>
  <a style="top:4480px" href="#">Contact</a>
</div>
<h5 style="position:absolute;left:587px;top:4305px;font-size:21px;font-weight:600;color:var(--white)">Contact</h5>
<div class="contact" style="top:4354px"><svg width="12" height="12" viewBox="0 0 24 24"><path fill="#fff" d="M6.6 10.8a15 15 0 006.6 6.6l2.2-2.2c.3-.3.7-.4 1-.2 1.1.4 2.3.6 3.6.6.6 0 1 .4 1 1V20c0 .6-.4 1-1 1A17 17 0 013 4c0-.6.4-1 1-1h3.5c.6 0 1 .4 1 1 0 1.3.2 2.5.6 3.6.1.3 0 .7-.2 1z"/></svg>+1 555 014 2297</div>
<div class="contact" style="top:4416px"><svg width="13" height="10" viewBox="0 0 26 20"><path fill="#fff" d="M0 0h26v20H0z"/><path fill="none" stroke="#2ba6e1" stroke-width="2" d="M1 1l12 10L25 1"/></svg>hello@veltrametrics.example</div>
<div class="contact" style="top:4478px"><svg width="10" height="14" viewBox="0 0 20 28"><path fill="#fff" d="M10 0a10 10 0 0110 10c0 7-10 18-10 18S0 17 0 10A10 10 0 0110 0z"/><circle cx="10" cy="10" r="4" fill="#2ba6e1"/></svg>123,Lorem ipsum dolor sit</div>
<h5 style="position:absolute;left:826px;top:4305px;font-size:21px;font-weight:600;color:var(--white)">Subscribe</h5>
<div class="abs" style="left:829px;top:4352px;width:259px;height:42px;border-radius:21px;background:var(--white);font-size:13px;color:var(--grey);padding:12px 24px">Email Address</div>
<div class="abs pill" style="left:829px;top:4404px;width:259px;height:42px;background:var(--blue-deep);color:var(--white);letter-spacing:2px">Subscribe Us</div>
<div class="social">
  <span role="img" aria-label="Social link" style="left:868px"></span>
  <span role="img" aria-label="Social link" style="left:914px"></span>
  <span role="img" aria-label="Social link" style="left:960px"></span>
  <span role="img" aria-label="Social link" style="left:1006px"></span>
</div>
<div class="abs" style="left:0;top:4601px;width:1200px;text-align:center;font-size:12px;color:var(--white)">© Copyright 2020 Veltra Metrics, All Rights Reserved.</div>

</body>
</html>
```